Brimsett Gardening Fresh New Website

We are looking to create a simple fresh website for our landscaping business. The website should appeal to a 'high end' audience. We deal with a lot of Embassies and affluent clients who have extremely large gardens that are meticulously maintained. The site is about communicating our excellent landscaping and customer service skills and encouraging new clients to reach out and engage us to take care of their gardens.

The website is basically going to be our business card, it will have almost no functionality other than two 'contact us' forms, one for smaller clients and one for more detailed projects.

The website will not have a lot of written content and will have to show photos of beautifully landscaped gardens.

The main logo in black will influence the site, however, we are open to all suggestions.

We are expecting to have the following pages:
Home Page
Services
About Us
Contact Us
Showcase (photo gallery of our work)

We need someone who can code it to wordpress and be available for minor changes over a number of days. They will be simple tweaks.

```html
<!DOCTYPE html>
<html lang="en">
<head>
<meta charset="utf-8">
<title>Brimsett Gardening</title>
<link href="https://fonts.googleapis.com/css2?family=Libre+Baskerville:wght@400;700&family=Montserrat:wght@400;500;600;700&display=swap" rel="stylesheet">
<style>
:root{
  --gold:#c39a45;
  --gold-deep:#9b7228;
  --gold-light:#f2cb55;
  --gold-btn-dark:#c4902a;
  --ink:#2e2e2e;
  --field:#2a2a2a;
  --grey:#e6e6e6;
  --white:#ffffff;
}
*{box-sizing:border-box;margin:0;padding:0}
html,body{width:1200px;height:4751px;overflow:hidden}
body{position:relative;background:var(--white);font-family:"Montserrat",sans-serif;color:var(--ink)}
.abs{position:absolute}
.btn{position:absolute;display:flex;align-items:center;justify-content:center;background:linear-gradient(180deg,var(--gold-light),var(--gold-btn-dark));color:#2a2208;font-weight:700;font-size:14px;letter-spacing:.5px;border-radius:3px;box-shadow:0 3px 6px rgba(0,0,0,.25)}
.brush{position:absolute;height:6px;background:#1f1f1f;border-radius:50%}

/* header */
.site-header{left:0;top:0;width:1200px;height:87px;background:var(--white)}
.brand{position:absolute;left:110px;top:22px;display:flex;align-items:center;gap:12px}
.brand-dot{width:26px;height:26px;border-radius:50%;border:1.5px solid var(--gold)}
.brand-name{font-family:"Libre Baskerville",serif;color:var(--gold);font-size:15px;letter-spacing:4px;line-height:20px;text-transform:uppercase}
.nav a{position:absolute;top:36px;font-size:14px;font-weight:600;color:var(--ink);text-decoration:none}
.nav .active{color:var(--gold)}

/* hero */
.hero{left:0;top:87px;width:1200px;height:660px;background:linear-gradient(180deg,#5f9a3b 0%,#3f7d28 30%,#79b833 60%,#8cc43a 100%);clip-path:polygon(0 0,100% 0,100% 600px,0 660px)}
.hero-text{left:0;top:345px;width:1200px;text-align:center;color:#1c1c1c}
.hero-welcome{font-size:23px;letter-spacing:1px}
.hero-title{font-family:"Libre Baskerville",serif;font-size:50px;margin-top:6px;letter-spacing:.5px;white-space:nowrap}
.dots span{position:absolute;left:1151px;width:24px;height:24px;border-radius:50%;font-size:12px;color:#e8e8e8;display:flex;align-items:center;justify-content:center}
.dots .on{background:#1e1e1e;color:#fff}

/* quick contact band */
.quick-contact{left:0;top:686px;width:1200px;height:280px;background:linear-gradient(100deg,#b68c3a,#a8802f 40%,#c39c4c 70%,#8f6a25)}
.field{position:absolute;background:var(--field);color:#e9e9e9;font-size:13px;padding-left:18px;display:flex;align-items:center}
.field.area{align-items:flex-start;padding-top:14px}
.chev{position:absolute;right:16px;top:50%;width:9px;height:9px;border-right:2px solid #ddd;border-bottom:2px solid #ddd;transform:translateY(-70%) rotate(45deg)}
.h-section{font-family:"Libre Baskerville",serif;font-weight:400;font-size:35px;line-height:44px;color:var(--ink);white-space:nowrap}
.h-section .accent{color:var(--gold)}
.h-contact{font-size:32px}
.h-about{font-size:31px}

/* about */
.about-photo{left:90px;top:1113px;width:430px;height:430px;border:4px solid #b07a35;border-radius:4px;background:linear-gradient(180deg,#a9cbe6 0%,#6e8f58 35%,#4e8a2f 60%,#79b53b 100%)}
.about-text{left:577px;top:1242px;width:470px;font-size:14.5px;line-height:24.5px;text-align:justify;color:#333}

/* services */
.services{left:0;top:1627px;width:1200px;height:916px;background:var(--grey);clip-path:polygon(0 65px,100% 0,100% 100%,0 100%)}
.card{position:absolute;width:300px;height:262px;border-radius:8px;box-shadow:0 5px 10px rgba(0,0,0,.35);overflow:hidden}
.card-frame{position:absolute;left:12px;top:12px;right:12px;bottom:12px;border:1px solid rgba(214,178,90,.8);border-radius:8px}
.card-shade{position:absolute;left:0;right:0;bottom:0;height:110px;background:linear-gradient(180deg,rgba(20,20,20,0),rgba(20,20,20,.85))}
.card-title{position:absolute;left:0;right:0;bottom:30px;text-align:center;font-family:"Libre Baskerville",serif;font-weight:700;font-size:16px;color:#e7c24f}

/* showcase */
.tile{position:absolute;width:222px;height:222px;border-radius:4px}

/* booking */
.booking{left:0;top:3364px;width:1200px;height:737px;background:linear-gradient(100deg,#c8a54e,#b69039 45%,#a57b2c 75%,#8e651f);clip-path:polygon(0 68px,100% 0,100% 100%,0 100%)}
.booking-lead{left:150px;top:3582px;width:900px;text-align:center;font-size:14.5px;line-height:24px;color:#2b2410}

/* footer */
.footer-col h4{position:absolute;font-size:16px;font-weight:700;color:var(--ink)}
.footer-col a{position:absolute;font-size:12px;color:#555;text-decoration:none}
.footer-scene{left:0;top:4400px;width:1200px;height:351px;background:linear-gradient(180deg,rgba(255,255,255,1) 0%,#9fc46a 25%,#4f8a2b 60%,#6aa436 100%)}
</style>
</head>
<body>

<header class="site-header abs">
  <div class="brand"><span class="brand-dot"></span><span class="brand-name">Brimsett Gardening</span></div>
  <nav class="nav">
    <a class="active" style="left:501px">HOME</a>
    <a style="left:590px">SERVICES</a>
    <a style="left:704px">ABOUT US</a>
    <a style="left:822px">SHOWCASE</a>
  </nav>
  <div class="btn" style="left:942px;top:22px;width:145px;height:44px">CONTACT US</div>
</header>

<section class="quick-contact abs" role="img" aria-label="Gold toned garden backdrop"></section>

<section class="hero abs" role="img" aria-label="Landscaped park with a stepping stone path across a lawn"></section>
<svg class="abs" style="left:0;top:680px" width="1200" height="70"><line x1="0" y1="67" x2="1200" y2="7" stroke="#3a2e14" stroke-width="4"/></svg>

<div class="hero-text abs">
  <div class="hero-welcome">WELCOME TO</div>
  <div class="hero-title">BRIMSETT GARDENING</div>
</div>
<div class="btn" style="left:527px;top:453px;width:146px;height:45px">GET STARTED</div>
<div class="dots">
  <span class="on" style="top:417px">01</span>
  <span style="top:449px">02</span>
  <span style="top:479px">03</span>
  <span style="top:510px">04</span>
  <span style="top:541px">05</span>
</div>

<h2 class="h-section h-contact abs" style="left:186px;top:810px">CONTACT US</h2>
<div class="brush" style="left:186px;top:878px;width:165px"></div>
<div class="field" style="left:475px;top:802px;width:266px;height:42px">Your Name *</div>
<div class="field" style="left:752px;top:802px;width:265px;height:42px">Phone Number *</div>
<div class="field" style="left:475px;top:861px;width:266px;height:42px">Email *</div>
<div class="btn" style="left:752px;top:858px;width:265px;height:46px;border:2px solid #f7e29a">SEND MESSAGE</div>

<div class="about-photo abs" role="img" aria-label="Manor house behind clipped topiary and a wide lawn"></div>
<h2 class="h-section h-about abs" style="left:577px;top:1150px"><span class="accent">ABOUT</span> BRIMSETT GARDENING</h2>
<div class="brush" style="left:577px;top:1216px;width:165px"></div>
<p class="about-text abs">Saerspiciatis undeasepoiise oklasdo mnis aidaste natus error sit voluptatem accusan tium doloremque laudantium, totam rem aperiam, ease aque ipaefdsa quae ab illo inventore veritatis ease quasi architecto beatae vitae dicta sunt explicabo. Nemo enim ipsam voluptatem quia volasdfupta sde sessitasese aspernatur autodit aut fugitsdsed quisaea consequuntur magni dolores eos qui ratione voluptatem sequi nesciunt.</p>
<div class="btn" style="left:577px;top:1449px;width:145px;height:44px">LEARN MORE</div>

<section class="services abs"></section>
<svg class="abs" style="left:0;top:1624px" width="1200" height="72"><line x1="0" y1="68" x2="1200" y2="3" stroke="#c9a24e" stroke-width="5"/></svg>
<h2 class="h-section abs" style="left:0;top:1787px;width:1200px;text-align:center"><span class="accent">OUR</span> SERVICES</h2>
<div class="brush" style="left:517px;top:1853px;width:165px"></div>

<div class="card" style="left:112px;top:1902px;background:linear-gradient(180deg,#c9536a,#6b9a3e 45%,#4f8a2c)" role="img" aria-label="Flowering azaleas beside a garden path"><div class="card-shade"></div><div class="card-frame"></div><div class="card-title">KOASLKE SEINASE</div></div>
<div class="card" style="left:452px;top:1902px;background:linear-gradient(180deg,#8a4e3a,#6a8d3a 45%,#4e7d2b)" role="img" aria-label="Garden bench among hedges"><div class="card-shade"></div><div class="card-frame"></div><div class="card-title">KOASLKE SEINASE</div></div>
<div class="card" style="left:789px;top:1902px;background:linear-gradient(180deg,#d9e6d2,#7b9a5a 45%,#566b4a)" role="img" aria-label="Park lawn with young trees"><div class="card-shade"></div><div class="card-frame"></div><div class="card-title">KOASLKE SEINASE</div></div>
<div class="card" style="left:112px;top:2193px;background:linear-gradient(180deg,#d4e3ee,#3f7a26 35%,#a83a2a 50%,#5d9b2e)" role="img" aria-label="Row of trees above red shrubs"><div class="card-shade"></div><div class="card-frame"></div><div class="card-title">KOASLKE SEINASE</div></div>
<div class="card" style="left:452px;top:2193px;background:linear-gradient(180deg,#e9ecea,#a8b79c 40%,#5f7b45 70%,#6f9343)" role="img" aria-label="Grassland with scattered trees"><div class="card-shade"></div><div class="card-frame"></div><div class="card-title">KOASLKE SEINASE</div></div>
<div class="card" style="left:789px;top:2193px;background:linear-gradient(180deg,#4aa8e0,#6cab37 40%,#c33a26 60%,#5aa12b)" role="img" aria-label="Red flower beds on a green lawn"><div class="card-shade"></div><div class="card-frame"></div><div class="card-title">KOASLKE SEINASE</div></div>

<h2 class="h-section abs" style="left:0;top:2633px;width:1200px;text-align:center;color:var(--gold)">SHOWCASE</h2>
<div class="brush" style="left:517px;top:2690px;width:165px"></div>
<div class="tile" style="left:112px;top:2731px;background:linear-gradient(180deg,#e7eef2,#4d7d2d 45%,#7bb43a)" role="img" aria-label="Tree on a sunlit lawn"></div>
<div class="tile" style="left:365px;top:2731px;background:linear-gradient(180deg,#4f8a2d,#6c8a78 55%,#3c6a28)" role="img" aria-label="Wooden deck among plants"></div>
<div class="tile" style="left:616px;top:2731px;background:linear-gradient(180deg,#d9e7cf,#5d9a34 45%,#c9c4b8)" role="img" aria-label="Paved walkway lined with palms"></div>
<div class="tile" style="left:868px;top:2731px;background:linear-gradient(180deg,#3e6d2a,#b34a93 45%,#8a7f70)" role="img" aria-label="Stone stairs with purple blossoms"></div>
<div class="tile" style="left:112px;top:2978px;background:linear-gradient(180deg,#6f9a3c,#4f8532 45%,#bcb8ab)" role="img" aria-label="Flagstone path through shrubs"></div>
<div class="tile" style="left:365px;top:2978px;background:linear-gradient(180deg,#d8e6f0,#3f7a26 40%,#63a52e)" role="img" aria-label="Open lawn with tree line"></div>
<div class="tile" style="left:616px;top:2978px;background:linear-gradient(180deg,#e0eadc,#3e6f27 40%,#9a9585)" role="img" aria-label="Curving stone path under trees"></div>
<div class="tile" style="left:868px;top:2978px;background:linear-gradient(180deg,#dfe9d6,#8dae5a 35%,#d56a4a 55%,#4aa32a)" role="img" aria-label="Flowering shrubs on a lawn"></div>
<div class="btn" style="left:527px;top:3236px;width:146px;height:45px">VIEW MORE</div>

<section class="booking abs" role="img" aria-label="Gold toned estate garden backdrop"></section>
<svg class="abs" style="left:0;top:3360px" width="1200" height="76"><line x1="0" y1="72" x2="1200" y2="4" stroke="#9b7228" stroke-width="5"/></svg>
<h2 class="h-section abs" style="left:0;top:3493px;width:1200px;text-align:center">BOOK A SERVICE</h2>
<div class="brush" style="left:517px;top:3553px;width:165px;height:5px"></div>
<p class="booking-lead abs">Saerspiciatis undeasepoiise oklasdo mnis aidaste natus error sit voluptatem accusan tium doloremque laudantium, totam rem aperiam, ease aque ipaefdsa quae</p>
<div class="field" style="left:181px;top:3651px;width:412px;height:41px">First Name *</div>
<div class="field" style="left:606px;top:3651px;width:411px;height:41px">Last Name *</div>
<div class="field" style="left:181px;top:3710px;width:412px;height:42px">Email *</div>
<div class="field" style="left:606px;top:3710px;width:411px;height:42px">Phone Number *</div>
<div class="field" style="left:181px;top:3771px;width:412px;height:40px">Services *<span class="chev"></span></div>
<div class="field" style="left:606px;top:3771px;width:411px;height:40px">Location *<span class="chev"></span></div>
<div class="field area" style="left:181px;top:3830px;width:836px;height:125px">Enter Your Message *</div>
<div class="btn" style="left:468px;top:3968px;width:264px;height:46px;border:2px solid #f7e29a">SEND MESSAGE</div>

<footer>
  <div class="footer-scene abs" role="img" aria-label="Row of palm trees along a landscaped park"></div>
  <div class="abs" style="left:211px;top:4200px;width:214px;text-align:center">
    <div style="width:34px;height:34px;border-radius:50%;border:1.5px solid var(--gold);margin:0 auto 20px"></div>
    <div class="brand-name" style="font-size:19px;line-height:30px">Brimsett Gardening</div>
  </div>
  <div class="footer-col">
    <h4 style="left:523px;top:4158px">QUICK LINKS</h4>
    <div class="abs" style="left:523px;top:4188px;width:55px;height:2px;background:var(--gold)"></div>
    <a style="left:525px;top:4204px">Home</a><a style="left:525px;top:4230px">Services</a><a style="left:525px;top:4256px">About Us</a><a style="left:525px;top:4282px">Contact Us</a>
    <h4 style="left:710px;top:4158px">LINKS</h4>
    <div class="abs" style="left:710px;top:4188px;width:50px;height:2px;background:var(--gold)"></div>
    <a style="left:711px;top:4204px">Copyright</a><a style="left:711px;top:4230px">Legal</a><a style="left:711px;top:4256px">Privacy</a><a style="left:711px;top:4282px">Accessibility</a><a style="left:711px;top:4308px">Sitemap</a>
    <h4 style="left:887px;top:4158px">SUPPORT</h4>
    <div class="abs" style="left:887px;top:4188px;width:50px;height:2px;background:var(--gold)"></div>
    <a style="left:889px;top:4204px">Team</a><a style="left:889px;top:4230px">About Us</a><a style="left:889px;top:4256px">Careers</a><a style="left:889px;top:4282px">Our Values</a>
  </div>
  <div class="abs" style="left:112px;top:4368px;width:976px;height:2px;background:var(--gold)"></div>
  <p class="abs" style="left:0;top:4386px;width:1200px;text-align:center;font-size:12px;color:#333">© Copyright 2024. All Rights Reserved.</p>
</footer>

</body>
</html>
```